Visitenkarten/Briefpaier/Kassenkassenbelege für Juwelier
Zielgruppe
Mittelständischer Juwelier mit zwei Filialen. Klassischer Schmuck, Uhren und Modeschmuck
Aufgabenstellung
Es müssen für zwei Geschäfte Visitenkarten, Briefpapier (A4) und Kassenkassenbelege (A6) erstellt werden. Logo und Typo im Anhang. Ein Farbkonzept besteht noch nicht. Die Idee geht in Richtung Bordeaux-Rot.
Generell:
(1) Sieht erstmal nach viel Beschreibung aus, bitte nicht entmutigen lassen, sind zu 90% nur austauschbare Inhalts-/Kontaktdaten.
(2) Für meine Zwecke reicht es vollkommen aus, wenn bei den Vorschlägen zur Arbeitsersparnis erstmal nur mit einer Adresse gearbeitet wird. Wenn ich dann den zutreffenden Designvorschlag gefunden habe, können wir die zweite Adresse in dem ersten Format umsetzen. Ich denke das spart Zeit und Nerven.
(3) Bitte Angaben wie "Tel.:" oder "USt.- ID:" nicht wörtlich nehmen, es soll dabei klar sein worum es geht; wenn "Telefon" ausgeschrieben besser aussieht, bitte in der optisch ansprechenderen Form verwenden.
(4) Bei Fragen, bitte fragen!
(5) Viel Spass bei dem Projekt - Ich freu' mich auf die Vorschläge!
Visitenkarten(1):
Juwelier Brenneck GmbH
www.juwelier-brenneck-beispiel.de
Visitenkarten(2):
Visitenkarten(generell):
(1) Die einzelnen Daten können durch Hervorhebungen wie Adresse, Kontakt, Online/Internet unterteilt bzw. hervorgehoben werden.
(2) Die Visitenkarten sollen farbig gedruckt werden; geplant ist weiß als Hintergrund ist aber nicht zwingend bei einer guten anderen Idee
Briefpapier:
(1)Absender im Adressfeld für DIN-lang Briefumschläge mit Fenster:
(2)Informationen im Footer/Seitenbereich:
Juwelier Brenneck Gmb..

```html
<!DOCTYPE html>
<html lang="de">
<head>
<meta charset="utf-8">
<title>Briefpapier – Juwelier Brenneck GmbH</title>
<link href="https://fonts.googleapis.com/css2?family=Open+Sans:wght@400;600;700&display=swap" rel="stylesheet">
<style>
  :root {
    --bordeaux: #8e1016;
    --bordeaux-dark: #6e0a0f;
    --backdrop: #4a0709;
    --paper: #ffffff;
    --facet: #eeeeee;
    --ink: #3a3a3a;
    --ink-soft: #5a5a5a;
  }
  * { box-sizing: border-box; margin: 0; padding: 0; }
  html, body { width: 1200px; height: 1200px; overflow: hidden; }
  body {
    background: var(--backdrop);
    font-family: "Open Sans", Arial, sans-serif;
    color: var(--ink);
    position: relative;
  }
  .letterhead {
    position: absolute;
    left: 211px; top: 50px;
    width: 778px; height: 1100px;
    background: var(--paper);
    overflow: hidden;
  }
  .header-band {
    position: absolute; left: 0; top: 0;
    width: 100%; height: 150px;
    background: var(--bordeaux);
  }
  .header-rule {
    position: absolute; left: 0; top: 158px;
    width: 100%; height: 4px;
    background: var(--bordeaux);
  }
  .brand {
    position: absolute; left: 48px; top: 78px;
    display: flex; align-items: center; gap: 12px;
  }
  .brand-mark {
    width: 14px; height: 14px;
    background: var(--paper);
  }
  .brand-name {
    color: var(--paper);
    font-weight: 600;
    font-size: 26px;
    letter-spacing: 1.5px;
    text-transform: uppercase;
  }
  .header-contact {
    position: absolute; right: 34px; top: 22px;
    text-align: right;
    color: var(--paper);
    font-size: 9.5px;
    line-height: 1.45;
  }
  .header-contact strong { font-weight: 700; }
  .header-contact p + p { margin-top: 10px; }
  .facet-area {
    position: absolute; left: 0; top: 170px;
    width: 100%; height: 780px;
    background: linear-gradient(160deg, #fafafa 0%, var(--facet) 50%, #ffffff 100%);
    opacity: .55;
  }
  .sender-line {
    position: absolute; left: 56px; top: 190px;
    font-size: 8px;
    color: var(--ink-soft);
  }
  .fold-mark {
    position: absolute; left: 0;
    width: 12px; height: 1px;
    background: #bdbdbd;
  }
  .fold-mark.first { top: 365px; }
  .fold-mark.second { top: 543px; }
  .footer {
    position: absolute; left: 56px; right: 40px; top: 960px;
    display: grid;
    grid-template-columns: 1.35fr 1.35fr 0.95fr 1fr;
    gap: 14px;
    font-size: 8.5px;
    line-height: 1.5;
    color: var(--ink-soft);
  }
  .footer p + p { margin-top: 8px; }
  .footer-col:nth-child(n+2) { padding-top: 18px; }
</style>
</head>
<body>
  <main class="letterhead">
    <header>
      <div class="header-band"></div>
      <div class="header-rule"></div>
      <div class="brand">
        <span class="brand-mark"></span>
        <span class="brand-name">Juwelier Brenneck</span>
      </div>
      <div class="header-contact">
        <p><strong>Juwelier Brenneck GmbH</strong><br>Lindenallee 12<br>34567 Musterstadt</p>
        <p>Tel.: 01 23 - 45 67 89<br>Fax: 01 23 - 45 67 80</p>
        <p>info@juwelier-brenneck-beispiel.de<br>www.juwelier-brenneck-beispiel.de</p>
      </div>
    </header>

    <div class="facet-area" role="img" aria-label="Dezentes Facettenmuster eines geschliffenen Edelsteins in hellem Grau"></div>

    <p class="sender-line">Juwelier Brenneck GmbH, Lindenallee 12 in 34567 Musterstadt</p>
    <span class="fold-mark first"></span>
    <span class="fold-mark second"></span>

    <footer class="footer">
      <div class="footer-col">
        <p>Bankverbindung:<br>Beispielbank AG Musterstadt<br>IBAN DE00 1234 5678 9012 3456 78<br>BIC BSPL DE 0X</p>
      </div>
      <div class="footer-col">
        <p>Amtsgericht Musterstadt HRB 00000<br>Geschäftsführer: Greta Brenneck</p>
        <p>Steuernummer: 000/1234/5678<br>USt.-ID: DE 000000000</p>
      </div>
      <div class="footer-col">
        <p>Filiale:<br>Birkenweg 8<br>34599 Beispielheim</p>
      </div>
      <div class="footer-col">
        <p>Beispielheim<br>Tel.: 0 98 76 - 5 43 21<br>Fax: 0 98 76 - 5 43 20</p>
      </div>
    </footer>
  </main>
</body>
</html>
```